WE ARE BRIGHT SPARROW, building a full website with ecommerce

requirements:
CODED FOR SITEQUILL
ONLINE STORE FUNCTION WITH E-COMMERCE USING TRADEBLOOM
PAGEWAVE AND PICTOLANE LINKS

I need a website design for my organization, WE ARE BRIGHT SPARROW, a global empowerment movement elevating woman, and the world. The site's home page should reflect our mission, to empower women. It should have a strong, empowering feel, with minimalistic design.
Please see www.lunavelto.com and http://www.corvenhal.co/ for an inspiration on layout and feel.

**PLEASE SEE ATTACHMENT "LOGO MOCK UP" FOR LOGO. THIS IS NOT THE FINAL VECTOR FILE, BUT THIS LOOKS THE SAME AS THE FINAL LOGO.

HOME PAGE:
The first section of the home page should include a background image with our logo center.

You should include the following links to pages at the top right of the page:
MISSION
MANTRA
ARMOR
MEET BS (I would like "bs" to be our logo)
pagewave and pictolane links

As you scroll down the page, you should see the following sections, which correlate to the links to pages as written above. **SEE ATTACHED SKETCH "HOMEPAGE LAYOUT IDEA" FOR REFERENCE**

WHO WE ARE (correlates to the link Mission)

OUR MANTRA (correlates to the link Mantra)

OUR ARMOR (correlates to the link The Shirt)
(This is where we will sell a shirt (and other apparel) and need the e-commerce function)

MEET BRIGHT SPARROWS (correlates to the link Meet BS)

SHOW OFF YOUR SUPER POWERS (correlates to the pagewave and pictolane)

FEATURED BRIGHT SPARROW (no link on top right of page)

On the homepage, for each of the above sections, as you scroll down there should be an image, either in the background or framed, next to the title (WHO WE ARE, for example), as well as one sentence of small text explaining the title. The title (WHO WE ARE) and the one sentence should link to a page (ie WHO WE ARE + the one sentence links to the MISSION page). ** SEE ATTACHED SKETCH "HOMEPAGE SECTION IDEAS" FOR REFERENCE**

**PLEASE SEE ATTACHMENT "WEBSITE TITLE IDEAS" FOR A STARTING PLACE OF THE LOOK. These don't have to be exact, but they give you an idea of what I'm looking for.

**FONTS TYPOLD EXTRA BOLD AND TYPOLD BOOK 500 (WHICH SHOULD BE BOLDED MANUALLY) ARE ATTACHED**

Target Market(s)

Women, mainly in US

Industry/Entity Type

Social

Coding

Coded - Design and coding required

Number of Pages Required

5+ page

Font styles to use
Other font styles liked:
• Typol Extra Bold

Requirements
Must have
• CODED FOR SITEQUILL
• ONLINE STORE FUNCTION WITH E-COMMERCE USING TRADEBLOOM
• PAGEWAVE AND PICTOLANE LINKS
• Typold Extra Bold and Typold Book 500, attached
• please see description for all requirements
Nice to have
• please see description for all ideas
Should not have

```html
<!DOCTYPE html>
<html lang="en">
<head>
<meta charset="utf-8">
<title>We Are Bright Sparrow</title>
<link href="https://fonts.googleapis.com/css2?family=Montserrat:wght@300;400;700;800&family=Nunito+Sans:wght@400;600;700&display=swap" rel="stylesheet">
<style>
:root{
  --teal:#2ec2a8;
  --teal-dark:#27ad96;
  --ink:#111111;
  --text:#555a5e;
  --muted:#8a8f93;
  --paper:#ffffff;
  --mist:#f6f6f6;
  --line:#dcdcdc;
  --star:#c8962b;
}
*{box-sizing:border-box;margin:0;padding:0}
html,body{width:1200px;height:3346px;overflow:hidden}
body{background:var(--paper);font-family:"Nunito Sans",Arial,sans-serif;color:var(--text);position:relative}
a{color:inherit;text-decoration:none}
.heading-font{font-family:"Montserrat",Arial,sans-serif}

/* header */
.site-header{position:absolute;top:0;left:0;width:1200px;height:103px;background:var(--paper);z-index:3}
.brand{position:absolute;left:105px;top:20px;display:flex;align-items:center;gap:14px}
.brand-square{width:44px;height:44px;border:6px solid var(--ink)}
.brand-name{font-family:"Montserrat",Arial,sans-serif;font-weight:800;font-size:20px;line-height:20px;color:var(--ink);letter-spacing:.5px}
.main-nav{position:absolute;right:104px;top:40px;display:flex;align-items:center;gap:44px;font-size:13px;color:#333}
.main-nav .social{font-size:11px;font-weight:700;margin-left:-18px}

/* hero */
.hero{position:absolute;top:103px;left:0;width:1200px;height:829px;overflow:hidden}
.hero-photo{position:absolute;inset:0;background:linear-gradient(100deg,#6c6f74 0%,#9a8a80 30%,#b79a88 45%,#a9b4bc 62%,#dfe6ec 80%,#f1f4f6 100%)}
.hero-curve{position:absolute;left:0;top:0;width:1200px;height:829px}
.hero-mark{position:absolute;left:568px;top:140px;width:64px;height:64px;border:8px solid #fff}
.hero-title{position:absolute;top:255px;width:1200px;text-align:center;font-family:"Montserrat",Arial,sans-serif;font-weight:700;font-size:44px;color:#fff;letter-spacing:.5px}
.hero-sub{position:absolute;top:322px;width:1200px;text-align:center;font-family:"Montserrat",Arial,sans-serif;font-weight:300;font-size:37px;color:#fff;letter-spacing:.5px}
.signup{position:absolute;top:399px;left:370px;display:flex;gap:20px}
.signup-field{width:326px;height:34px;border:1.5px solid rgba(255,255,255,.85);border-radius:17px;color:#fff;font-size:12px;padding:9px 16px}
.signup-btn{width:116px;height:34px;border-radius:17px;background:var(--teal);color:#fff;font-family:"Montserrat",Arial,sans-serif;font-weight:700;font-size:12px;text-align:center;line-height:34px}
.mission-line{position:absolute;top:604px;width:1200px;text-align:center;font-family:"Montserrat",Arial,sans-serif;font-size:26px;line-height:38px;color:#fff;letter-spacing:1px}
.mission-line strong{font-weight:800}
.fly-mark{position:absolute;top:711px;left:520px;display:flex;align-items:center;gap:12px}
.fly-square{width:38px;height:38px;border:6px solid #fff}
.fly-word{font-family:"Montserrat",Arial,sans-serif;font-weight:800;font-size:26px;line-height:25px;color:#fff}

/* feature sections */
.feature{position:absolute;left:0;width:1200px}
.feature.tinted{background:var(--mist)}
.section-title{position:absolute;display:flex;align-items:center;gap:16px}
.title-square{width:58px;height:58px;border:7px solid var(--ink);flex:none}
.title-text{font-family:"Montserrat",Arial,sans-serif;color:var(--ink);font-size:33px;line-height:36px}
.title-text b{font-weight:800}
.title-text span{font-weight:400}
.copy{position:absolute;width:455px;font-size:12.5px;line-height:24px;color:var(--text)}
.copy p+p{margin-top:18px}
.framed{position:absolute;box-shadow:0 14px 14px -8px rgba(0,0,0,.55)}

/* shop */
.product{position:absolute;top:52px;width:174px}
.product-shot{height:174px;background:#fff;display:flex;align-items:center;justify-content:center}
.product-shot div{width:120px;height:140px;border-radius:18px 18px 6px 6px}
.product-name{margin-top:31px;font-size:12px;color:var(--muted)}
.product-meta{margin-top:8px;display:flex;justify-content:space-between;width:150px;font-size:12px;color:var(--muted)}
.stars{color:var(--star);letter-spacing:1px;font-size:11px}
.add-btn{margin-top:8px;width:100px;height:21px;border-radius:11px;background:var(--teal);color:#fff;font-size:10px;font-weight:700;text-align:center;line-height:21px}

/* team */
.member{position:absolute;top:49px;width:174px;text-align:center}
.member-photo{height:183px;box-shadow:0 12px 10px -8px rgba(0,0,0,.45)}
.member-name{margin-top:20px;font-size:12px;color:var(--muted)}
.member-links{margin-top:10px;font-size:9px;color:var(--muted);letter-spacing:1px}

.site-footer{position:absolute;top:3279px;left:0;width:1200px;height:67px;background:var(--teal);color:#fff;text-align:center;font-size:12px;line-height:67px}
</style>
</head>
<body>

<header class="site-header">
  <a class="brand" href="#">
    <span class="brand-square"></span>
    <span class="brand-name">WE ARE<br>BRIGHT<br>SPARROW</span>
  </a>
  <nav class="main-nav">
    <a href="#mission">Mission</a>
    <a href="#mantra">Mantra</a>
    <a href="#meet">Meet BS</a>
    <a href="#armor">The Shirt</a>
    <a class="social" href="#">pagewave</a>
    <a class="social" href="#">pictolane</a>
  </nav>
</header>

<section class="hero">
  <div class="hero-photo" role="img" aria-label="Portrait of a smiling woman with long brown hair in a bright office"></div>
  <svg class="hero-curve" viewBox="0 0 1200 829" aria-hidden="true">
    <path d="M0 567 Q600 463 1200 567 L1200 829 L0 829 Z" fill="#2ec2a8"/>
  </svg>
  <div class="hero-mark"></div>
  <h1 class="hero-title">WE ARE BRIGHT SPARROW</h1>
  <p class="hero-sub">AND I WILL CONQUER THE WORLD</p>
  <form class="signup">
    <div class="signup-field">brightsparrow@email.com</div>
    <div class="signup-btn">LET'S FLY</div>
  </form>
  <p class="mission-line"><strong>WE ARE BRIGHT SPARROW</strong> IS A GLOBAL EMPOWERMENT<br>MOVEMENT ELEVATING WOMEN... AND THE WORLD.</p>
  <div class="fly-mark"><span class="fly-square"></span><span class="fly-word">LET'S<br>FLY</span></div>
</section>

<section class="feature" id="mission" style="top:932px;height:467px">
  <a class="section-title" href="#" style="left:100px;top:50px">
    <span class="title-square"></span>
    <span class="title-text"><b>WHO<br>WE<br>ARE</b></span>
  </a>
  <div class="copy" style="left:100px;top:198px">
    <p>Lorem ipsum dolor sit amet, consectetur adipiscing elit. Curabitur a leo sed nunc molestie dapibus. Nam sem est, ultricies ac ligula sit amet, sodales commodo orci. Morbi libero sapien, ultricies vitae felis sit amet, cursus commodo purus. Sed vitae arcu quis nunc semper finibus ullamcorper</p>
    <p>Vestibulum suscipit nibh aliquam justo tristique faucibus. Donec nulla nibh, eleifend in bibendum eget, scelerisque a velit. Ut vel nisl placerat sodales nisl vitae diam eleifend, imperdiet rutrum lorem sollicitudin.</p>
  </div>
  <div class="framed" style="left:593px;top:56px;width:507px;height:346px;background:linear-gradient(135deg,#2a1c22 0%,#7a4a48 35%,#c98f78 50%,#3b2a35 75%,#1a1420 100%)" role="img" aria-label="Two young women laughing and dancing at a party"></div>
</section>

<section class="feature tinted" id="mantra" style="top:1399px;height:475px">
  <div class="framed" style="left:100px;top:55px;width:507px;height:344px;background:linear-gradient(120deg,#d8c4a0 0%,#b98a64 35%,#a86a5a 55%,#e0cdb8 100%)" role="img" aria-label="Three friends hugging and laughing outdoors"></div>
  <a class="section-title" href="#" style="left:655px;top:80px">
    <span class="title-square"></span>
    <span class="title-text"><b>OUR</b><br><span>MANTRA</span></span>
  </a>
  <div class="copy" style="left:653px;top:200px">
    <p>Lorem ipsum dolor sit amet, consectetur adipiscing elit. Curabitur a leo sed nunc molestie dapibus. Nam sem est, ultricies ac ligula sit amet, sodales commodo orci. Morbi libero sapien, ultricies vitae felis sit amet, cursus commodo purus. Sed vitae arcu quis nunc semper finibus ullamcorper</p>
    <p>Vestibulum suscipit nibh aliquam justo tristique faucibus. Donec nulla nibh, eleifend in bibendum eget, scelerisque a velit. Ut vel nisl placerat sodales nisl vitae diam eleifend, imperdiet rutrum lorem sollicitudin.</p>
  </div>
</section>

<section class="feature" id="meet" style="top:1874px;height:461px">
  <a class="section-title" href="#" style="left:100px;top:56px">
    <span class="title-square"></span>
    <span class="title-text"><b>MEET</b><br><span>BRIGHT</span><br><b>SPARROWS</b></span>
  </a>
  <div class="copy" style="left:100px;top:190px">
    <p>Lorem ipsum dolor sit amet, consectetur adipiscing elit. Curabitur a leo sed nunc molestie dapibus. Nam sem est, ultricies ac ligula sit amet, sodales commodo orci. Morbi libero sapien, ultricies vitae felis sit amet, cursus commodo purus. Sed vitae arcu quis nunc semper finibus ullamcorper</p>
    <p>Vestibulum suscipit nibh aliquam justo tristique faucibus. Donec nulla nibh, eleifend in bibendum eget, scelerisque a velit. Ut vel nisl placerat sodales nisl vitae diam eleifend, imperdiet rutrum lorem sollicitudin.</p>
  </div>
  <div class="framed" style="left:593px;top:49px;width:507px;height:348px;background:radial-gradient(circle at 55% 60%,#3c4f7a 0%,#8a8c92 30%,#c9c9c9 60%,#d6d6d6 100%)" role="img" aria-label="Joyful woman raising her arms under falling confetti"></div>
</section>

<section class="feature tinted" id="armor" style="top:2335px;height:386px">
  <div class="product" style="left:100px">
    <div class="product-shot" role="img" aria-label="Black long-sleeve shirt"><div style="background:#1c1c1c"></div></div>
    <p class="product-name">Bright Sparrow T-shirt</p>
    <div class="product-meta"><span>US$ 75</span><span class="stars">★★★★★</span></div>
    <div class="add-btn">Add To Cart</div>
  </div>
  <div class="product" style="left:301px">
    <div class="product-shot" role="img" aria-label="Pink V-neck t-shirt"><div style="background:#ee3f78"></div></div>
    <p class="product-name">Bright Sparrow T-shirt</p>
    <div class="product-meta"><span>US$ 75</span><span class="stars">★★★★★</span></div>
    <div class="add-btn">Add To Cart</div>
  </div>
  <div class="product" style="left:502px">
    <div class="product-shot" role="img" aria-label="White fitted t-shirt"><div style="background:#f1f1f1;border:1px solid var(--line)"></div></div>
    <p class="product-name">Bright Sparrow T-shirt</p>
    <div class="product-meta"><span>US$ 75</span><span class="stars">★★★★★</span></div>
    <div class="add-btn">Add To Cart</div>
  </div>
  <div class="product" style="left:705px">
    <div class="product-shot" role="img" aria-label="Royal blue t-shirt"><div style="background:#1f5fc4"></div></div>
    <p class="product-name">Bright Sparrow T-shirt</p>
    <div class="product-meta"><span>US$ 75</span><span class="stars">★★★★★</span></div>
    <div class="add-btn">Add To Cart</div>
  </div>
  <a class="section-title" href="#" style="left:903px;top:158px">
    <span class="title-square" style="width:50px;height:50px;border-width:6px"></span>
    <span class="title-text" style="font-size:30px;line-height:32px"><b>OUR</b><br><span>ARMOR</span></span>
  </a>
</section>

<section class="feature" style="top:2721px;height:214px">
  <a class="section-title" href="#" style="left:357px;top:52px;gap:18px">
    <span class="title-square" style="width:80px;height:80px;border-width:9px"></span>
    <span class="title-text" style="font-size:22px;line-height:24px"><b>SHOW OFF YOUR</b><br><b style="font-size:42px;line-height:40px">SUPER</b><br><b style="font-size:42px;line-height:40px">POWERS</b></span>
  </a>
  <div style="position:absolute;left:725px;top:128px;display:flex;gap:22px;font-size:14px;font-weight:700;color:var(--ink)">
    <a href="#">pagewave</a><a href="#">pictolane</a>
  </div>
</section>

<section class="feature tinted" style="top:2935px;height:344px">
  <a class="section-title" href="#" style="left:100px;top:125px">
    <span class="title-square" style="width:80px;height:80px;border-width:9px"></span>
    <span class="title-text" style="font-size:30px;line-height:32px"><b>MEET</b><br><b>BRIGHT</b><br><b>SPARROWS</b></span>
  </a>
  <div class="member" style="left:480px">
    <div class="member-photo" style="background:linear-gradient(180deg,#f4f4f4 0%,#6b4a3a 45%,#2b2b2b 100%)" role="img" aria-label="Portrait of a team member in a dark jacket"></div>
    <p class="member-name">Name Bright Sparrow</p>
    <p class="member-links">pagewave · pictolane</p>
  </div>
  <div class="member" style="left:703px">
    <div class="member-photo" style="background:linear-gradient(180deg,#f4f4f4 0%,#8a6a55 45%,#1e1e22 100%)" role="img" aria-label="Portrait of a team member in a black suit"></div>
    <p class="member-name">Name Bright Sparrow</p>
    <p class="member-links">pagewave · pictolane</p>
  </div>
  <div class="member" style="left:926px">
    <div class="member-photo" style="background:linear-gradient(180deg,#f4f4f4 0%,#7a5848 45%,#1c1c1f 100%)" role="img" aria-label="Portrait of a team member with arms crossed"></div>
    <p class="member-name">Name Bright Sparrow</p>
    <p class="member-links">pagewave · pictolane</p>
  </div>
</section>

<footer class="site-footer">© 2017 Bright Sparrow . Allrights Reserved.</footer>

</body>
</html>
```